TL - business card

Tallow Partners is an insurance brokerage firm, inovative, proactive, vigorous, which aims to become the leader of the insurance brokers in Anfrica. We should like to get some designs which should be avoided also in Gray / Metallic for the Administration and Orange / Blue for the Managers (ike in the picture sent). The Blue / Green logo is not the correct one, but the source of the file. Please adjust the color accordingly for the business cards. 1 / Orange / Blue 2 / Gray / Metallic We want something classic but which is transmitted strenght, inovation, modernity and most of all, rapidity. We want something start-up like, very punchy and catching eye remaining profesional at the same time. Name: Dorian Whitlock Function: Managing Director Address: N ° 17/18 Rua Veloso - R / C 2B Direita - Bairro Mutamba - Luanda Tel: (+244) 947 582 316 Email: dorian.whitlock@tallow-p.example Website: www.tallow-p. example We want classic in the front and creative, colorfull at the back. The cards will be printed in relief, with very high quality of paper.
Insurance Broker
Colors
Designer to choose colors to be used in the design.

```html
<!DOCTYPE html>
<html lang="en">
<head>
<meta charset="utf-8">
<title>Tallow Partners – Business Card</title>
<link rel="stylesheet" href="https://fonts.googleapis.com/css2?family=Exo+2:wght@500;600&family=Lato:wght@400&display=swap">
<style>
  :root {
    --orange: #f06a22;
    --blue: #2aa9e0;
    --ink: #222222;
    --rule: #555555;
    --paper: #ffffff;
    --backdrop: #2b2b2b;
  }
  * { margin: 0; padding: 0; box-sizing: border-box; }
  html, body { width: 1200px; height: 1200px; overflow: hidden; }
  body { background: var(--backdrop); position: relative; font-family: "Lato", sans-serif; }

  .card {
    position: absolute;
    top: 310px;
    width: 364px;
    height: 594px;
    box-shadow: 0 4px 10px rgba(0,0,0,.5);
  }
  .card-front { left: 234px; background: var(--paper); text-align: center; color: var(--ink); }
  .card-back { left: 627px; overflow: hidden; }

  .brand-mark {
    position: absolute;
    left: 132px; top: 95px;
    width: 100px; height: 100px;
    border: 7px solid var(--orange);
    border-radius: 50%;
  }
  .brand-name {
    position: absolute;
    left: 0; right: 0; top: 203px;
    font-family: "Exo 2", sans-serif;
    font-weight: 600;
    font-size: 27px;
    letter-spacing: .5px;
    color: var(--orange);
  }

  .contact { position: absolute; left: 0; right: 0; top: 362px; }
  .person-name {
    font-family: "Exo 2", sans-serif;
    font-weight: 500;
    font-size: 22px;
    line-height: 26px;
  }
  .person-name .first { color: var(--orange); }
  .person-name .last { color: var(--blue); }
  .person-role { font-size: 16px; line-height: 20px; }
  .divider { width: 156px; height: 1px; background: var(--rule); margin: 8px auto 8px; }
  .detail { font-size: 16px; line-height: 22px; }

  .back-art { display: block; width: 100%; height: 100%; }
</style>
</head>
<body>
  <section class="card card-front">
    <div class="brand-mark"></div>
    <div class="brand-name">TALLOW PARTNERS</div>
    <div class="contact">
      <div class="person-name"><span class="first">DORIAN</span> <span class="last">WHITLOCK</span></div>
      <div class="person-role">Managing Director</div>
      <div class="divider"></div>
      <div class="detail">(+244) 947 582 316</div>
      <div class="detail">dorian.whitlock@tallow-p.example</div>
      <div class="divider"></div>
      <div class="detail">N ° 17/18 Rua Veloso - R / C</div>
      <div class="detail">2B Direita</div>
      <div class="detail">Bairro Mutamba - Luanda</div>
    </div>
  </section>

  <section class="card card-back">
    <svg class="back-art" viewBox="0 0 364 594" role="img" aria-label="Large white illustration of a rising rocket over an orange and blue diagonal split">
      <rect width="364" height="594" fill="var(--blue)"/>
      <polygon points="0,0 364,0 364,110 0,538" fill="var(--orange)"/>
    </svg>
  </section>
</body>
</html>
```